Web Design Project

We have a website in beta that needs updating and are looking for a freash new look for the Home page including Logo.
Our company is called " Kip Dorra " we specialize in classified advertising using video. Our consumers will be businesses selling a product or service. Please visit www.kipdorra.com
Our aim past this point is to engage a developer to write the code based on the best design. Our target market is the U.S and I have included some of the landing pages to give you a better idea of what we are trying to acheive

http://www.kipdorra.com/
http://www.kipdorra.com/cars_home.php
http://www.kipdorra.com/boats.php
http://www.kipdorra.com/electronic.php
http://www.kipdorra.com/realestate.php
http://www.kipdorra.com/roommates.php
Updates

Target Market(s)

20-35 yr old people who are connected to the internet via mobile phone and use social media on a daily/weekly basis

Industry/Entity Type

Advertising

Requirements
Must have
• We would like to use lots of images to convey it is a video driven website business
Nice to have
• Logo to incorporate same theme of website ( ie ) you are here to watch videos of thinhs to buy & sell
Should not have
• This is to be a freash new site with large type and bold fonts

```html
<!DOCTYPE html>
<html lang="en">
<head>
<meta charset="utf-8">
<title>Kip Dorra – Video Classifieds</title>
<link rel="stylesheet" href="https://fonts.googleapis.com/css2?family=Open+Sans:wght@400;600;700&family=Roboto+Condensed:wght@400;700&display=swap">
<style>
:root{
  --red:#c8191b;
  --red-dark:#a80f10;
  --orange:#ee6a1f;
  --ink:#444;
  --dark:#222;
  --bg:#f3f3f3;
  --panel:#fff;
  --footer:#dcdcdc;
  --footer-bar:#c6c6c6;
  --grey-btn:#4a4a4a;
}
*{box-sizing:border-box;margin:0;padding:0}
html,body{width:950px;height:1200px;overflow:hidden}
body{position:relative;background:var(--bg);font-family:"Open Sans",sans-serif;color:var(--ink)}
.abs{position:absolute}

/* header */
.site-header{left:95px;top:0;width:756px;height:120px;background:var(--panel);box-shadow:0 2px 6px rgba(0,0,0,.12)}
.top-line{left:0;top:0;width:950px;height:2px;background:#2b5d9a}
.brand{left:130px;top:40px}
.brand-name{display:flex;align-items:center;gap:10px;font-family:"Roboto Condensed",sans-serif;font-weight:700;font-size:42px;color:var(--red);line-height:1}
.brand-dot{width:16px;height:16px;border-radius:50%;background:var(--red)}
.lang{left:713px;top:19px;width:121px;height:21px;border:1px solid #bbb;background:#fff;font-size:9px;font-style:italic;color:#999;display:flex;align-items:center;padding-left:6px;gap:6px}
.lang .flag{width:15px;height:10px;background:#2a3d8f;border:1px solid #c00}
.lang .caret{margin-left:auto;margin-right:8px;font-style:normal;color:#333}
.action-panel{left:421px;top:53px;width:425px;height:67px;border:1px solid #ddd;border-bottom:none;border-radius:6px 6px 0 0;background:linear-gradient(#fafafa,#e9e9e9)}
.btn{position:absolute;height:27px;border-radius:3px;color:#fff;font-family:"Roboto Condensed",sans-serif;font-size:13px;display:flex;align-items:center;justify-content:center;box-shadow:0 1px 2px rgba(0,0,0,.4)}
.btn-dark{background:linear-gradient(#333,#111)}
.btn-red{background:linear-gradient(#d8282a,#a81012)}
.search{left:668px;top:75px;width:167px;height:25px;border-radius:3px;background:linear-gradient(#8a8a8a,#6a6a6a);color:#eee;font-size:9px;display:flex;align-items:center;padding-left:16px}
.search .go{position:absolute;right:4px;top:3px;width:19px;height:19px;background:var(--red);border:1px solid #fff}

/* category nav */
.cat-nav{left:0;top:126px;width:950px;height:44px;background:linear-gradient(#5a5a5a,#1a1a1a 60%,#000)}
.cat{position:absolute;top:0;height:44px;display:flex;align-items:center;gap:6px;color:#fff;font-size:12.5px}
.cat svg{fill:#ddd}

/* hero */
.hero{left:0;top:170px;width:950px;height:288px;background:linear-gradient(90deg,#b81214,#d62a24 60%,#c41a1a)}
.hero-shadow{left:120px;top:452px;width:720px;height:16px;border-radius:50%;background:rgba(0,0,0,.25);filter:blur(6px)}
.player{left:91px;top:183px;width:435px;height:262px;background:#000}
.player-frame{left:59px;top:28px;width:317px;height:181px;background:linear-gradient(135deg,#9a9a9a,#5c5c5c 50%,#2b2b2b);border:1px solid #666}
.play-box{left:285px;top:276px;width:48px;height:50px;background:rgba(30,30,30,.8);color:#fff;font-size:8px;text-align:center;padding-top:6px}
.controls{left:91px;top:421px;width:435px;height:24px;background:linear-gradient(#333,#111);color:#fff;font-size:7px}
.track{left:55px;top:10px;width:240px;height:3px;background:#555}
.bitrate{left:334px;top:4px;width:60px;height:16px;border:1px solid #666;border-radius:2px;font-size:7.5px;padding:2px 6px}
.hero-title{left:550px;top:224px;font-family:"Roboto Condensed",sans-serif;font-weight:700;font-size:18px;color:#fff;text-shadow:0 1px 2px rgba(0,0,0,.4)}
.hero-rule{left:550px;top:251px;width:325px;height:1px;background:rgba(255,255,255,.2)}
.hero-copy{left:552px;top:258px;width:310px;font-size:10px;line-height:16.6px;color:#fde3e0}
.btn-more{left:554px;top:354px;width:80px;height:32px;background:linear-gradient(#555,#222);border-radius:3px;color:#fff;font-family:"Roboto Condensed",sans-serif;font-size:13px;display:flex;align-items:center;justify-content:center;box-shadow:0 1px 3px rgba(0,0,0,.5)}
.dots{left:793px;top:414px;display:flex;gap:5px}
.dots span{width:11px;height:11px;border-radius:50%;background:#111;border:1px solid #555}
.dots span.on{background:#eee}

/* featured */
.section-title{font-family:"Roboto Condensed",sans-serif;font-weight:700;font-size:16.5px;color:#444}
.tab{position:absolute;top:486px;height:26px;border-radius:3px;color:#fff;font-family:"Roboto Condensed",sans-serif;font-weight:700;font-size:11px;display:flex;align-items:center;justify-content:center;box-shadow:0 1px 2px rgba(0,0,0,.3)}
.tab-active{background:linear-gradient(#d8282a,#a81012)}
.tab-idle{background:linear-gradient(#666,#333)}
.thumb{position:absolute;width:225px;height:130px;background:#fff;border:1px solid #ccc;box-shadow:0 6px 6px -4px rgba(0,0,0,.2);padding:6px 8px}
.thumb .media{width:100%;height:100%;border:1px solid #2a3a8a}
.featured-bg{left:0;top:470px;width:950px;height:354px;background:linear-gradient(#f6f6f6,#ececec)}
.works-bg{left:0;top:824px;width:950px;height:214px;background:#fff}

/* how it works */
.step{position:absolute;width:124px;height:124px;border-radius:50%;background:#fff;border:2px solid #ddd;overflow:hidden;box-shadow:0 2px 6px rgba(0,0,0,.2)}
.step-top{position:absolute;left:0;top:0;width:100%;height:32px;background:var(--orange);color:#fff;font-family:"Roboto Condensed",sans-serif;font-weight:700;font-size:15px;text-align:center;padding-top:10px}
.step-mid{position:absolute;left:0;top:48px;width:100%;display:flex;align-items:center;justify-content:center;gap:4px;font-family:"Roboto Condensed",sans-serif;font-weight:700;font-size:17px;color:#444}
.step-bot{position:absolute;left:24px;bottom:-16px;width:76px;height:34px;border-radius:50%;background:#222;color:#fff;font-family:"Roboto Condensed",sans-serif;font-size:9.5px;text-align:center;padding-top:5px}

/* footer */
.footer{left:0;top:1038px;width:950px;height:134px;background:var(--footer)}
.f-col{position:absolute;top:24px}
.f-col h4{font-family:"Roboto Condensed",sans-serif;font-weight:400;font-size:13px;color:#333;margin-bottom:6px}
.f-col li{list-style:none;font-size:9.5px;line-height:14.2px;color:#333}
.social{display:flex;gap:9px;margin-top:8px}
.social span{width:21px;height:21px;border:1px solid #fff;box-shadow:0 1px 2px rgba(0,0,0,.3)}
.footer-bar{left:0;top:1172px;width:950px;height:28px;background:var(--footer-bar);font-size:8.5px;color:#333;display:flex;align-items:center;justify-content:center}
</style>
</head>
<body>

<div class="abs top-line"></div>
<header class="abs site-header"></header>
<div class="abs brand">
  <div class="brand-name"><span class="brand-dot"></span>Kip Dorra</div>
</div>
<div class="abs lang"><span class="flag"></span>English<span class="caret">⌄</span></div>
<div class="abs action-panel"></div>
<a class="btn btn-dark" style="left:437px;top:74px;width:59px">BACK</a>
<a class="btn btn-red" style="left:501px;top:74px;width:98px">CREATE AN AD</a>
<a class="btn btn-dark" style="left:604px;top:74px;width:59px">SIGN IN</a>
<div class="abs search">SEARCH
  <span class="go"><svg width="17" height="17" viewBox="0 0 17 17"><circle cx="7.5" cy="7.5" r="3.5" fill="none" stroke="#fff" stroke-width="1.8"/><line x1="10" y1="10" x2="13" y2="13" stroke="#fff" stroke-width="2"/></svg></span>
</div>

<nav class="abs cat-nav">
  <div class="cat" style="left:106px"><svg width="34" height="18" viewBox="0 0 34 18"><path d="M2 12 L5 6 L12 4 L22 4 L28 8 L32 9 L32 13 L2 13Z"/><circle cx="9" cy="14" r="3"/><circle cx="25" cy="14" r="3"/></svg>Cars</div>
  <div class="cat" style="left:210px"><svg width="22" height="26" viewBox="0 0 22 26"><path d="M11 1 L11 19 L3 19Z"/><path d="M12 5 L19 19 L12 19Z"/><path d="M1 21 L21 21 L18 25 L4 25Z"/></svg>Boats</div>
  <div class="cat" style="left:307px"><svg width="24" height="24" viewBox="0 0 24 24"><circle cx="12" cy="12" r="11"/><rect x="8" y="5" width="2" height="5" fill="#555"/><rect x="14" y="5" width="2" height="5" fill="#555"/><path d="M7 10 H17 V13 A5 5 0 0 1 7 13Z" fill="#555"/></svg>Electronics</div>
  <div class="cat" style="left:443px"><svg width="20" height="20" viewBox="0 0 20 20"><path d="M10 1 L19 9 L16 9 L16 19 L4 19 L4 9 L1 9Z"/></svg>Real Estate</div>
  <div class="cat" style="left:565px"><svg width="26" height="20" viewBox="0 0 26 20"><circle cx="9" cy="6" r="4"/><path d="M1 19 A8 7 0 0 1 17 19Z"/><circle cx="18" cy="5" r="3.5"/><path d="M14 12 A7 6 0 0 1 25 17 L18 17Z"/></svg>Rommates</div>
  <div class="cat" style="left:698px"><svg width="18" height="22" viewBox="0 0 18 22"><rect x="5" y="1" width="12" height="16"/><rect x="1" y="5" width="12" height="16" stroke="#555" stroke-width="1"/></svg>Other Categories</div>
</nav>

<section class="abs hero" aria-label="Featured video"></section>
<div class="abs hero-shadow"></div>
<div class="abs player">
  <div class="abs player-frame" role="img" aria-label="Video still of a black convertible driving through a car lot"></div>
</div>
<div class="abs play-box">Play<br><svg width="10" height="12" viewBox="0 0 10 12" style="margin-top:6px"><path d="M1 0 L10 6 L1 12Z" fill="#fff"/></svg></div>
<div class="abs controls">
  <svg class="abs" style="left:8px;top:5px" width="10" height="13" viewBox="0 0 10 13"><path d="M0 0 L10 6.5 L0 13Z" fill="#ccc"/></svg>
  <span class="abs" style="left:27px;top:14px">00:00</span>
  <div class="abs track"></div>
  <span class="abs" style="left:280px;top:14px">01:13</span>
  <svg class="abs" style="left:310px;top:6px" width="16" height="12" viewBox="0 0 16 12"><path d="M0 4 H3 L7 0 V12 L3 8 H0Z" fill="#ccc"/><path d="M10 3 Q13 6 10 9 M12 1 Q16 6 12 11" stroke="#ccc" fill="none"/></svg>
  <div class="abs bitrate">900k<span style="position:absolute;right:5px">▴</span></div>
  <svg class="abs" style="left:404px;top:6px" width="12" height="12" viewBox="0 0 12 12"><path d="M0 4V0H4M8 0H12V4M12 8V12H8M4 12H0V8" stroke="#ccc" stroke-width="1.6" fill="none"/></svg>
</div>
<h1 class="abs hero-title">LOREM IPSUM DOLLAR SIT AMET</h1>
<div class="abs hero-rule"></div>
<p class="abs hero-copy">Cum sociis natoque penatibus et magnis dis parturient montes, nascetur ridiculus mus. In iaculis facilisis massa. Etiam eu urna. Sed porta.Cum sociis natoque penatibus et magnis dis parturient montes, nascetur ridiculus mus. In iaculis facilisis massa. Etiam eu urna. Sed porta.</p>
<a class="abs btn-more">MORE &gt;&gt;</a>
<div class="abs dots"><span class="on"></span><span></span><span></span><span></span></div>

<div class="abs featured-bg"></div>
<h2 class="abs section-title" style="left:91px;top:491px">BROWSE FEATURED KIP DORRA</h2>
<a class="tab tab-active" style="left:505px;width:107px">MOST VIEWED</a>
<a class="tab tab-idle" style="left:617px;width:106px">MOST RECENT</a>
<a class="tab tab-idle" style="left:728px;width:117px">MOST INTERESTING</a>

<div class="thumb" style="left:95px;top:524px"><div class="media" role="img" aria-label="Red sports car video" style="background:linear-gradient(135deg,#222,#8a1010 55%,#d42020)"></div></div>
<div class="thumb" style="left:348px;top:524px"><div class="media" role="img" aria-label="Motor yacht on open water" style="background:linear-gradient(160deg,#1d3f7a,#2f5c9a 50%,#15305e)"></div></div>
<div class="thumb" style="left:602px;top:524px"><div class="media" role="img" aria-label="Large family house" style="background:linear-gradient(#6c95cc,#c9ccc0 55%,#8a8a6a)"></div></div>
<div class="thumb" style="left:95px;top:674px"><div class="media" role="img" aria-label="Handheld video camera" style="background:linear-gradient(135deg,#fff,#c8c8c8 55%,#8a8a8a)"></div></div>
<div class="thumb" style="left:348px;top:674px"><div class="media" role="img" aria-label="Two roommates sitting in a new apartment" style="background:linear-gradient(#b58a5c,#d8c0a0 60%,#c0a080)"></div></div>
<div class="thumb" style="left:602px;top:674px"><div class="media" role="img" aria-label="Passenger jet in a blue sky" style="background:linear-gradient(#1d63b8,#4a8fd8 60%,#a8cbee)"></div></div>

<div class="abs works-bg"></div>
<h2 class="abs section-title" style="left:91px;top:841px">HOW IT WORKS</h2>

<div class="step" style="left:173px;top:869px">
  <div class="step-top">STEP 1</div>
  <div class="step-mid"><svg width="30" height="22" viewBox="0 0 30 22"><circle cx="6" cy="5" r="4" fill="#667"/><circle cx="15" cy="5" r="4" fill="#667"/><rect x="1" y="9" width="20" height="11" rx="2" fill="#556"/><path d="M21 12 L29 8 L29 20 L21 16Z" fill="#556"/></svg>CREAT IT</div>
  <div class="step-bot">More</div>
</div>
<div class="step" style="left:348px;top:869px">
  <div class="step-top">STEP 2</div>
  <div class="step-mid"><svg width="26" height="28" viewBox="0 0 26 28"><rect x="1" y="1" width="16" height="22" fill="#eee" stroke="#bbb"/><circle cx="16" cy="18" r="8" fill="#3aa535"/><path d="M16 12 L21 18 H18 V23 H14 V18 H11Z" fill="#fff"/></svg>UPLOAD IT</div>
  <div class="step-bot">More</div>
</div>
<div class="step" style="left:515px;top:869px">
  <div class="step-top">STEP 3</div>
  <div class="step-mid"><svg width="36" height="26" viewBox="0 0 36 26"><path d="M1 3 H7 L11 18 H29 L33 7 H9" stroke="#888" stroke-width="2" fill="none"/><circle cx="13" cy="22" r="2.5" fill="#444"/><circle cx="27" cy="22" r="2.5" fill="#444"/></svg>SELL IT</div>
  <div class="step-bot">More</div>
</div>

<footer class="abs footer">
  <div class="f-col" style="left:97px"><h4>Buy / Browse</h4><ul><li>Roommates</li><li>Cars</li><li>Boats</li><li>Electronics</li><li>Others</li></ul></div>
  <div class="f-col" style="left:232px"><h4>Sell</h4><ul><li>Start Selling</li><li>Login</li><li>Shooting Video</li><li>Uploading Video</li><li>Buying</li></ul></div>
  <div class="f-col" style="left:367px"><h4>Info</h4><ul><li>VBlog</li><li>FAQs</li><li>Terms of Use</li><li>Privacy Policy</li><li>Buyer/Seller Safety</li></ul></div>
  <div class="f-col" style="left:502px"><h4>Contact</h4><ul><li>Contact Us</li><li>Feedback Form</li><li>Referral Program</li><li>Business Register</li><li>Subscription</li></ul></div>
  <div class="f-col" style="left:645px"><h4>Connect With Us</h4>
    <div class="social"><span style="background:#3b5a99"></span><span style="background:#3fb3e8"></span><span style="background:#333"></span><span style="background:#f0a030"></span><span style="background:#cc1a1a"></span><span style="background:#8aa6c0"></span></div>
  </div>
</footer>
<div class="abs footer-bar">© 2013 kipdorra.com, All Rights Reserved</div>

</body>
</html>
```